Business card

We need a business card design for our company based in Auckland , New Zealand called 'Ridge + Studio Ltd'. We provide architectural services. We would like to see designs that use the max. three colours (such as white, black, grey) The final design should communicate financial safety and growth."
Also I will provide our company logo. I would like to the logo to be embeded onto our business card.

Target Market(s)

new residential house, alteration & addition & light commericila design & drafting service

Industry/Entity Type

Architecture

Contact Information for Business Card

Company name: ridge + studio Ltd.
Name: Mark Delford
Job title: architectural designer & Design LBP
email address: mark@rplusd.co.nz
mobile number: 02 5163 2290
web site: www.rplusd.co.nz

Requirements
Must have
• My project must have..
• - embeded logo (attached company logo)
• I don't have a bigger version for our company logo, but I have one old one, so you can remove the word from it)
• - insert the attached small BKTW logo & LBP logo
• - creative, simple and clear business card.
• - Max. three colours
Nice to have
• - Here are the samples I would like to share with you: http://www.plimvora.com/blog/minimalistic-business-card-designs/
• I would like to have my business card like one of the creation.
Should not have
• TBA

```html
<!DOCTYPE html>
<html lang="en">
<head>
<meta charset="UTF-8">
<title>Ridge + Studio Ltd — Business Card</title>
<link rel="stylesheet" href="https://fonts.googleapis.com/css2?family=Raleway:wght@300;400;700&family=Oswald:wght@500&family=Roboto:wght@700&display=swap">
<style>
  :root {
    --canvas: #e6e6e4;
    --card-white: #ffffff;
    --charcoal: #3d3d3f;
    --ink: #111111;
    --soft-grey: #c9c9c9;
    --muted-grey: #8a8d87;
    --text-light: #e4e4e4;
  }
  * { margin: 0; padding: 0; box-sizing: border-box; }
  html, body {
    width: 1200px; height: 900px; overflow: hidden;
    background: var(--canvas);
  }
  .stage { position: relative; width: 1200px; height: 900px; }

  .card {
    position: absolute; left: 300px;
    width: 600px; height: 343px;
    background: var(--card-white);
    overflow: hidden;
    box-shadow: 0 6px 18px rgba(0,0,0,0.18);
  }
  .card--front { top: 80px; }
  .card--back { top: 465px; }

  /* Front */
  .front-mark {
    position: absolute; left: 50%; top: 52px;
    width: 150px; height: 150px; margin-left: -75px;
    border: 9px solid var(--ink); border-radius: 50%;
  }
  .name-banner {
    position: absolute; left: 50%; top: 232px;
    width: 340px; height: 36px; margin-left: -170px;
    background: var(--ink);
    clip-path: polygon(4% 0, 100% 0, 96% 50%, 100% 100%, 4% 100%, 0 50%);
    display: flex; align-items: center; justify-content: center;
    font-family: "Oswald", sans-serif; font-weight: 500;
    font-size: 21px; color: var(--card-white); letter-spacing: 0.2px;
  }

  /* Back */
  .dark-panel {
    position: absolute; left: 0; top: 0;
    width: 300px; height: 100%;
    background: var(--charcoal);
  }
  .person {
    position: absolute; left: 30px; top: 42px;
    font-family: "Raleway", sans-serif; color: var(--text-light);
  }
  .person__name { font-size: 29px; font-weight: 300; letter-spacing: 0.5px; line-height: 1; }
  .person__name strong { font-weight: 700; color: #f3f3f3; }
  .person__title { font-size: 14px; font-weight: 400; margin-top: 6px; }

  .contact-box {
    position: absolute; left: 10px; top: 148px;
    width: 338px; height: 165px;
    background: var(--charcoal);
    border: 5px solid var(--card-white);
    border-radius: 24px;
    padding: 28px 24px 0 0;
  }
  .contact-line {
    display: flex; justify-content: flex-end; align-items: center;
    gap: 12px; height: 38px;
    font-family: "Raleway", sans-serif; font-size: 17px;
    color: var(--soft-grey);
  }
  .contact-icon { width: 24px; height: 24px; flex: none; }

  .badge-practitioner {
    position: absolute; left: 420px; top: 88px;
    width: 78px; height: 78px; border-radius: 50%;
    background: var(--ink);
  }
  .badge-member {
    position: absolute; left: 418px; top: 200px;
    width: 44px; height: 34px;
    background: var(--charcoal);
  }
  .member-label {
    position: absolute; left: 424px; top: 244px;
    font-family: "Roboto", sans-serif; font-weight: 700;
    font-size: 11px; line-height: 1.2; color: var(--muted-grey);
  }
</style>
</head>
<body>
<main class="stage">

  <section class="card card--front" aria-label="Card front">
    <div class="front-mark" aria-hidden="true"></div>
    <div class="name-banner">ridge + studio Ltd.</div>
  </section>

  <section class="card card--back" aria-label="Card back">
    <div class="dark-panel"></div>

    <div class="person">
      <p class="person__name">MARK <strong>DELFORD</strong></p>
      <p class="person__title">Architectural Designer &amp; Design LBP</p>
    </div>

    <div class="contact-box">
      <p class="contact-line">02 5163 2290
        <svg class="contact-icon" viewBox="0 0 24 24" aria-hidden="true">
          <circle cx="12" cy="12" r="12" fill="#fff"/>
          <rect x="8" y="5" width="8" height="14" rx="1.5" fill="none" stroke="#3d3d3f" stroke-width="1.6"/>
          <circle cx="12" cy="16.5" r="0.9" fill="#3d3d3f"/>
        </svg>
      </p>
      <p class="contact-line">www.rplusd.co.nz
        <svg class="contact-icon" viewBox="0 0 24 24" aria-hidden="true">
          <circle cx="12" cy="12" r="12" fill="#fff"/>
          <circle cx="12" cy="12" r="6.5" fill="none" stroke="#3d3d3f" stroke-width="1.6"/>
          <ellipse cx="12" cy="12" rx="2.8" ry="6.5" fill="none" stroke="#3d3d3f" stroke-width="1.3"/>
          <line x1="5.5" y1="12" x2="18.5" y2="12" stroke="#3d3d3f" stroke-width="1.3"/>
        </svg>
      </p>
      <p class="contact-line">mark@rplusd.co.nz
        <svg class="contact-icon" viewBox="0 0 24 24" aria-hidden="true">
          <circle cx="12" cy="12" r="12" fill="#fff"/>
          <rect x="6" y="8" width="12" height="8.5" rx="1" fill="#3d3d3f"/>
          <polyline points="6.5,8.6 12,13 17.5,8.6" fill="none" stroke="#fff" stroke-width="1.2"/>
        </svg>
      </p>
    </div>

    <div class="badge-practitioner" role="img" aria-label="Licensed building practitioner badge"></div>
    <div class="badge-member" role="img" aria-label="BKTW membership badge"></div>
    <p class="member-label">Professional<br>Member</p>
  </section>

</main>
</body>
</html>
```